Disability Service Provider Expo Banner that will stand out amongst the competition

We would like to have a two banners designed to be able to display at expos that outline the services that we provide as a company. We are a disability service provider who aims to provider services to increase the independence of those living with a disability. We would like the banners to follow consistent themes/designs from other marketing material that we have (see brief for designs). One of the banners will be for the allied health services we provide (exercise physiology and occupational therapy) and the other banner will be promoting the our support worker, programs, and short-term accommodation. Our main colour schemes for therapy are black, yellow, and white. For our other services we utilise yellow, blue, and magenta as part of our colour pallet. Please utilise the information from the flyers, colours, and logos all located in the design brief. The style of banner can be seen in the images upload in the brief.

Target Market(s)

Parents and carers of those who livce with a disability, and seeking their business over our competitors

Industry/Entity Type

Disability Service and Health Provider

Colors

Designer to choose colors to be used in the design.

Requirements
Must have
• Eye catching, limited text
Nice to have
• Split services across a few banners
Should not have
• Lots of words

```html
<!DOCTYPE html>
<html lang="en">
<head>
<meta charset="utf-8">
<title>Brightvale Pull-up Banners</title>
<link rel="stylesheet" href="https://fonts.googleapis.com/css2?family=Montserrat:ital,wght@0,400;0,500;0,600;0,700;0,800;1,800&display=swap">
<style>
  :root {
    --black: #000000;
    --yellow: #f2dc3c;
    --white: #ffffff;
    --grey-chip: #c9c9c9;
    --stage: #7f7f7f;
    --photo-dark: #1c2530;
    --photo-mid: #5b7790;
    --photo-light: #c6ced6;
  }
  * { box-sizing: border-box; margin: 0; padding: 0; }
  html, body { width: 1187px; height: 1200px; overflow: hidden; }
  body {
    background: var(--stage);
    font-family: "Montserrat", sans-serif;
    position: relative;
  }
  .banner {
    position: absolute;
    top: 120px;
    width: 406px;
    height: 925px;
    background: var(--black);
    color: var(--white);
    overflow: hidden;
  }
  .banner--therapy { left: 163px; }
  .banner--services { left: 616px; }

  .brand { position: absolute; left: 0; right: 0; top: 42px; text-align: center; }
  .brand__dot {
    width: 50px; height: 50px; border-radius: 50%;
    background: var(--yellow); margin: 0 auto 14px;
  }
  .brand__name {
    font-weight: 800; font-size: 42px; letter-spacing: 1px;
    color: var(--white); line-height: 1; text-transform: uppercase;
  }

  .headline {
    position: absolute; left: 0; right: 0; top: 190px;
    text-align: center; color: var(--yellow);
    font-weight: 800; font-size: 43px; line-height: 46px;
  }
  .intro {
    position: absolute; left: 0; right: 0; top: 290px;
    text-align: center; font-size: 17px; line-height: 22.5px; font-weight: 400;
  }
  .intro strong { font-weight: 700; }

  .photo-area {
    position: absolute; left: 0; right: 0; top: 375px; height: 345px;
    background:
      linear-gradient(180deg, var(--black) 0%, rgba(0,0,0,0) 22%, rgba(0,0,0,0) 72%, rgba(20,22,25,0.9) 100%),
      linear-gradient(120deg, var(--photo-dark) 0%, var(--photo-mid) 40%, var(--photo-light) 65%, var(--photo-dark) 100%);
  }
  .lower-fade {
    position: absolute; left: 0; right: 0; top: 720px; height: 100px;
    background: linear-gradient(180deg, #16181a 0%, #050505 100%);
  }

  .tags { position: absolute; top: 706px; left: 26px; right: 22px; display: flex; gap: 7px; }
  .tag {
    height: 33px; border-radius: 4px;
    display: flex; align-items: center; justify-content: center;
    font-weight: 800; font-style: italic; font-size: 15px; color: var(--black);
    background: var(--grey-chip); box-shadow: 0 3px 6px rgba(0,0,0,0.6);
  }
  .tag--fit { width: 106px; }
  .tag--healthy { width: 131px; background: var(--yellow); }
  .tag--fun { width: 107px; }

  .contact-cloud { position: absolute; left: 0; bottom: 0; width: 406px; height: 150px; }
  .contact {
    position: absolute; left: 0; right: 0; bottom: 38px;
    text-align: center; color: var(--black);
  }
  .contact__phone {
    font-size: 28px; font-weight: 500; line-height: 34px;
    display: flex; align-items: center; justify-content: center; gap: 6px;
  }
  .contact__phone strong { font-weight: 700; }
  .contact__web { font-size: 23px; font-weight: 500; line-height: 30px; }
  .contact__web strong { font-weight: 700; }

  .collage { position: absolute; left: 0; top: 170px; }

  .services-title {
    position: absolute; left: 28px; right: 28px; top: 604px; height: 30px;
    display: flex; align-items: center;
  }
  .services-title__rule { flex: 1; height: 2px; background: linear-gradient(90deg, transparent, #8a7a2a); }
  .services-title__rule--right { background: linear-gradient(90deg, #8a7a2a, transparent); }
  .services-title__label {
    background: var(--yellow); color: var(--black); font-weight: 800;
    font-size: 19px; padding: 0 10px; border-radius: 14px; line-height: 28px;
  }

  .services {
    position: absolute; left: 22px; right: 20px; top: 650px;
    display: grid; grid-template-columns: 110px 153px 1fr; grid-template-rows: 46px 60px;
  }
  .service {
    display: flex; align-items: center; justify-content: center;
    text-align: center; font-size: 16.5px; font-weight: 500; line-height: 20px;
  }
  .service--row1 { border-bottom: 2px dotted var(--yellow); padding-bottom: 4px; }
  .service--mid { border-left: 2px dotted var(--yellow); border-right: 2px dotted var(--yellow); }
  .services .service:nth-child(3) { padding-top: 0; }
</style>
</head>
<body>

<section class="banner banner--therapy">
  <div class="brand">
    <div class="brand__dot"></div>
    <div class="brand__name">Brightvale</div>
  </div>

  <h1 class="headline">EXERCISE<br>PHYSIOLOGY</h1>
  <p class="intro">Improve your <strong>health, quality of life,</strong><br><strong>&amp; independence</strong> with the help of<br>our Excersise Physiologist!</p>

  <div class="photo-area" role="img" aria-label="Photo: exercise physiologist guiding a client with a prosthetic leg through floor exercises in a gym"></div>
  <div class="lower-fade"></div>

  <div class="tags">
    <span class="tag tag--fit">GET FIT</span>
    <span class="tag tag--healthy">BE HEALTHY</span>
    <span class="tag tag--fun">HAVE FUN</span>
  </div>

  <svg class="contact-cloud" viewBox="0 0 406 150" aria-hidden="true">
    <path d="M0 48 Q14 40 27 46 C34 12 78 0 112 0 C146 0 170 20 186 38 C206 14 240 7 275 7 C322 7 356 30 380 60 Q393 53 406 50 V150 H0Z" fill="var(--yellow)"/>
  </svg>
  <div class="contact">
    <div class="contact__phone">
      <svg width="26" height="26" viewBox="0 0 26 26" aria-hidden="true">
        <circle cx="13" cy="13" r="13" fill="var(--black)"/>
        <path d="M9 7 l2.5 0 1 3.2 -1.6 1.2 c0.8 1.7 2 2.9 3.7 3.7 l1.2 -1.6 3.2 1 0 2.5 c-6 0.6 -10.6 -4 -10 -10z" fill="var(--yellow)"/>
      </svg>
      <span>Call <strong>1800 000 123</strong></span>
    </div>
    <div class="contact__web">www.<strong>brightvale.com</strong>.au</div>
  </div>
</section>

<section class="banner banner--services">
  <div class="brand">
    <div class="brand__dot"></div>
    <div class="brand__name">Brightvale</div>
  </div>

  <svg class="collage" width="406" height="420" viewBox="0 0 406 420" role="img" aria-label="Photo collage: support workers with clients, cooking workshop, group dance activity, farm outing and a gym session">
    <defs>
      <linearGradient id="g1" x1="0" y1="0" x2="1" y2="1"><stop offset="0" stop-color="#6b5a48"/><stop offset="1" stop-color="#1e1e22"/></linearGradient>
      <linearGradient id="g2" x1="0" y1="0" x2="1" y2="1"><stop offset="0" stop-color="#d9dde2"/><stop offset="1" stop-color="#3a3236"/></linearGradient>
      <linearGradient id="g3" x1="0" y1="0" x2="0" y2="1"><stop offset="0" stop-color="#3a5aa8"/><stop offset="1" stop-color="#8a5a30"/></linearGradient>
      <linearGradient id="g4" x1="0" y1="0" x2="0" y2="1"><stop offset="0" stop-color="#6f9ad0"/><stop offset="1" stop-color="#7a5236"/></linearGradient>
      <linearGradient id="g5" x1="0" y1="0" x2="1" y2="1"><stop offset="0" stop-color="#e4e6ea"/><stop offset="1" stop-color="#3a3a40"/></linearGradient>
    </defs>
    <circle cx="137" cy="252" r="98" fill="url(#g3)"/>
    <circle cx="277" cy="183" r="97" fill="url(#g2)" stroke="var(--yellow)" stroke-width="2"/>
    <circle cx="175" cy="107" r="97" fill="url(#g1)" stroke="var(--black)" stroke-width="6"/>
    <circle cx="175" cy="107" r="94" fill="none" stroke="var(--yellow)" stroke-width="2"/>
    <circle cx="253" cy="310" r="62" fill="url(#g4)" stroke="var(--black)" stroke-width="6"/>
    <circle cx="253" cy="310" r="59" fill="none" stroke="var(--yellow)" stroke-width="2"/>
    <circle cx="160" cy="356" r="56" fill="url(#g5)" stroke="var(--black)" stroke-width="6"/>
    <circle cx="160" cy="356" r="53" fill="none" stroke="var(--yellow)" stroke-width="2"/>
  </svg>

  <div class="services-title">
    <span class="services-title__rule"></span>
    <span class="services-title__label">Our Services</span>
    <span class="services-title__rule services-title__rule--right"></span>
  </div>

  <div class="services">
    <div class="service service--row1">Support<br>Workers</div>
    <div class="service service--row1 service--mid">Day Programs<br>&amp; Workshops</div>
    <div class="service service--row1">Group<br>Activities</div>
    <div class="service">Living Skills<br>Programs</div>
    <div class="service service--mid">STA/Supported<br>Holiday</div>
    <div class="service" style="align-items:flex-start;padding-top:8px">Therapies</div>
  </div>

  <svg class="contact-cloud" viewBox="0 0 406 150" aria-hidden="true">
    <path d="M0 55 Q14 48 27 56 C36 20 78 2 114 2 C150 2 172 22 188 40 C206 18 240 6 276 6 C322 6 355 34 378 62 Q392 56 406 54 V150 H0Z" fill="var(--yellow)"/>
  </svg>
  <div class="contact">
    <div class="contact__phone">
      <svg width="26" height="26" viewBox="0 0 26 26" aria-hidden="true">
        <circle cx="13" cy="13" r="13" fill="var(--black)"/>
        <path d="M9 7 l2.5 0 1 3.2 -1.6 1.2 c0.8 1.7 2 2.9 3.7 3.7 l1.2 -1.6 3.2 1 0 2.5 c-6 0.6 -10.6 -4 -10 -10z" fill="var(--yellow)"/>
      </svg>
      <span>Call <strong>1800 000 123</strong></span>
    </div>
    <div class="contact__web">www.<strong>brightvale.com</strong>.au</div>
  </div>
</section>

</body>
</html>
```